Harbor Lanterns Book Cover Design

Book Cover Design Brief:
Title: Harbor Lanterns
Author: Dena Morrow
đź§­ Subtitle:
A Handbook for the Woman in the Storm or Set to Begin
🎯 Badge Text:
A Compass for Women Navigating Transformation
Trim Size: 6 x 9 inches
Total Number of Pages: Estimate 204 pages (including front/back matter and section dividers).
⸻

đź§­ Overview

Harbor Lanterns is a powerful, faith-based guide and story collection written by Dena Morrow who shares stories of 12 other women. Each chapter offers real-life insight and encouragement for women walking through the emotional wilderness of life—divorce, grief, burnout, identity shifts, loss, and uncertainty. This book isn’t about being lost in nature—it’s about navigating the unseen wilderness of the heart and soul, and finding sacred direction through faith, sisterhood, and intentional self-discovery. It’s for the woman who feels alone in what she’s going through, and is ready to rise again—with strength, clarity, and support.
đź§­ The Compass Framework
The book is grounded in Dena Morrow’s Compass Framework: Community, Openness, Mindset, Purposeful Movement, Accountability, Support, and Self-Care. This 7-part model guides readers from feeling lost to finding purpose, and the compass symbol should appear on the cover as a subtle but meaningful visual representing that inner journey.
🎨 Design Direction Must Haves
• A single woman in a wilderness-like setting (open field, mist, shoreline, etc.), visually representing emotional solitude and personal reflection • A compass or symbolic directional element integrated into the design (can be subtle—part of the background, light, path, etc.) •Mood should reflect quiet strength, inner transformation, hope and sacred guidance
Color palette: Deep greens, earthy tones, and warm golden or divine light—evoking grounding, hope, and spiritual depth
Title: Harbor Lanterns
• “Wilderness” in a natural, elegant font (same as The Harbor Lantern logo if possible) “Wisdom” in a bold serif to evoke strength and maturity
đź§­ Subtitle:
Author Name: Dena Morrow (centered or lower third, clean serif font)
Badge Text: 🎯 Badge Text:
(discreet, bottom right or near author name—no drop shadows)

Nice to Haves: Subtle visual cues of sisterhood or support in the distance (faint outlines, footsteps, horizon silhouettes) • Divine light or glow to represent God’s presence • Natural textures like breeze, water, or mist to evoke movement and transition •A sense of forward momentum—even if the woman is standing still
Should Not Have •Literal forest survival imagery •Cold or overly corporate fonts •Harsh primary colors or visual clutter
Back Cover / Spine Note The design should flow naturally into the spine and back cover. The compass and wilderness elements should feel part of the world, not placed on top of it.
Back Cover Description:
Harbor Lanterns is a healing guide and collection of real stories from women who have walked through life’s hardest seasons. Divorce, grief, abandonment, illness, burnout, addiction, estrangement, narcissistic abuse, homelessness, and the loss of loved ones are all part of the emotional wilderness this book speaks to.
If you feel lost, stuck, or unsure of who you are now, you are not alone. This book is for the woman standing in the middle of her wilderness, ready to take the next step toward healing and purpose.
Each chapter offers real truth and practical encouragement, with reflections that point you back to your strength, your True North, and the life you were made for.
Harbor Lanterns helps you reclaim faith, power, and purpose through the Compass Framework, a path shaped by values like community, mindset, and self-care.
Harbor Lanterns is a healing guide and collection of real stories from women who have walked through life’s hardest seasons. Written by life and business coach Dena Morrow, the book shares her personal journey alongside the voices of 12 courageous women. Divorce, grief, abandonment, illness, burnout, addiction, estrangement, narcissistic abuse, homelessness, and the loss of loved ones are all part of the emotional wilderness this book speaks to.

Whether you are standing in the fire or ready to rise from it, this book was written to meet you there. It is for the woman who feels stuck, shaken, or unsure of who she is now and knows something within her is ready to heal.

Each chapter offers truth and encouragement, with reflections that point you back to your strength, your True North, and the life you were made for.

With every page, you are reminded that you are not lost. You are finding your way as you engage with Dena’s story, the experiences of 12 other women, apply the tools, and move forward with clarity and courage.

Author Bio:
Dena Morrow is a life and business coach, speaker, and author who empowers women to reclaim their faith, power, and purpose after life has shaken their foundation. As the founder of The Harbor Lantern, she helps women move forward with clarity and confidence through seasons of change, loss, and transformation.

Through her coaching, workshops, and writing, Dena creates spaces where women stop feeling stuck and start rising, equipped with tools, community, and a renewed sense of direction for the life ahead.

Target Market(s)

Women ages 30-80

Industry/Entity Type

Faith Based Self Help, Spiritual Growth • Christian Living / Women’s Issues • Faith-Based Personal Development • Self-Help / Spiritual • Women’s Empowerment • Personal Transformation

Font styles to use
Serif
Sans Serif

Requirements
Must have
• A cover that visually reflects the emotional wilderness women experience during life transitions—grief, divorce, abandonment, identity loss, loss of loved one, estrangement, addiction, burnout, etc.—and the sacred path toward hope, strength, and purpose • A design that communicates both solitude and resilience, with visual cues that suggest faith, guidance, and transformation • A compass symbol or directional element subtly integrated to represent the Compass Framework (Community, Openness, Mindset, Purposeful Movement, Accountability, Support, Self-Care) • The overall tone should be inspiring, reflective, and spiritually grounded—not clinical, overly modern, or corporate • Designers are encouraged to explore concepts involving a single woman or symbolic imagery that evokes personal journey and inner navigation • Use of natural elements (landscape, light, sky, mist, etc.) is welcomed but not required—designers may propose abstract, minimalist, or layered concepts that align with the book’s message • Include the following text: • Title: Harbor Lanterns • Subtitle: đź§­ Subtitle: A Handbook for the Woman in the Storm or Set to Begin 🎯 Badge Text: A Compass for Women Navigating Transformation • Author: Dena Morrow •If you are using women they need to be real, diverse in age between 30-80 , body type and demographics
Nice to have
• A woman (or symbolic figure) in the design to reflect the personal, emotional journey of transformation • Subtle visual references to faith, sisterhood, or unseen support (e.g., faint silhouettes, glowing light, soft horizon figures, or abstract representations) • Creative use of natural elements like fog, water, paths, or sky to symbolize movement, mystery, or healing • A warm, layered color palette that transitions from darkness or shadow into light—suggesting hope and divine guidance • Textured or painterly backgrounds that feel organic and timeless • Compass elements woven into the environment (not pasted on top)—integrated as part of the visual metaphor • A sense of emotional depth or quiet strength that draws the viewer in • A design that would appeal to a wide age range of women (not too youthful or too somber)
Should not have
• Literal or clichĂ© wilderness imagery that feels like survival gear, camping, or rugged outdoor adventure • Harsh or neon colors, overly bright palettes, or anything that feels “salesy” or corporate • Clip art, cartoon-style illustrations, or flat graphics that lack emotional depth • Fonts that are overly modern, decorative, or hard to read—especially script fonts that look informal or casual • Designs that feel cold, sterile, masculine, or tech-driven • Cluttered layouts or elements that distract from the core message of faith, reflection, and transformation • Any portrayal that makes the woman look hopeless or abandoned—this is a story of resilience and rising, not despair. • A “sorority” or exclusive club feel—this book should never appear as if it’s only for a select group or the “cool girls” • Any design that suggests perfection, status, or elitism—this is about raw, real life, and inner healing • Glamour-focused imagery that disconnects from authenticity or emotional depth

```html
<!DOCTYPE html>
<html lang="en">
<head>
<meta charset="utf-8">
<title>Harbor Lanterns — Book Cover</title>
<link rel="stylesheet" href="https://fonts.googleapis.com/css2?family=Bebas+Neue&family=Montserrat:wght@400;500;600&display=swap">
<style>
  :root {
    --backdrop: #bcbdbf;
    --ink-black: #050302;
    --title-white: #f7fbfd;
    --author-gold: #f5c265;
    --rule-gold: #c9953f;
    --seal-light: #f6e3a4;
    --seal-mid: #d8b263;
    --seal-deep: #b88a3a;
    --tagline: #1a1208;
  }
  html, body {
    margin: 0;
    width: 1200px;
    height: 1200px;
    overflow: hidden;
    background: var(--backdrop);
  }
  .cover {
    position: absolute;
    left: 221px;
    top: 31px;
    width: 757px;
    height: 1137px;
    background: var(--ink-black);
    overflow: hidden;
  }
  .cover-photo {
    position: absolute;
    inset: 0 0 103px 0;
    background:
      radial-gradient(ellipse 60% 22% at 40% 14%, rgba(255,252,230,0.95), rgba(255,240,180,0) 70%),
      radial-gradient(ellipse 35% 30% at 52% 52%, rgba(60,28,10,0.75), rgba(60,28,10,0) 75%),
      linear-gradient(180deg, #fbf3cf 0%, #f6dc8e 14%, #e9b552 30%, #cf8a2e 46%, #9a5a1b 60%, #4a2a0f 74%, #140a04 88%, var(--ink-black) 100%);
  }
  .subtitle {
    position: absolute;
    top: 54px;
    left: 0;
    width: 100%;
    margin: 0;
    text-align: center;
    font-family: "Montserrat", sans-serif;
    font-weight: 400;
    font-size: 18.5px;
    letter-spacing: 0.2px;
    color: var(--tagline);
  }
  .subtitle-rule {
    position: absolute;
    top: 92px;
    left: 149px;
    width: 459px;
    height: 2px;
    background: linear-gradient(90deg, rgba(201,149,63,0), var(--rule-gold) 20%, var(--rule-gold) 80%, rgba(201,149,63,0));
  }
  .seal {
    position: absolute;
    left: 520px;
    top: 440px;
    width: 174px;
    height: 174px;
  }
  .seal-text {
    position: absolute;
    inset: 0;
    display: flex;
    align-items: center;
    justify-content: center;
    text-align: center;
    font-family: "Montserrat", sans-serif;
    font-weight: 600;
    font-size: 15px;
    line-height: 19px;
    color: #120c04;
  }
  .title {
    position: absolute;
    left: 0;
    top: 0;
    width: 757px;
    height: 1137px;
  }
  .title text {
    font-family: "Bebas Neue", sans-serif;
    fill: var(--title-white);
  }
  .author {
    position: absolute;
    top: 1046px;
    left: 0;
    width: 100%;
    height: 56px;
    display: flex;
    align-items: center;
    gap: 22px;
  }
  .author-rule {
    flex: 1;
    height: 2px;
    background: var(--rule-gold);
  }
  .author-name {
    flex: none;
    font-family: "Montserrat", sans-serif;
    font-weight: 500;
    font-size: 48px;
    line-height: 56px;
    letter-spacing: 1px;
    color: var(--author-gold);
  }
</style>
</head>
<body>
  <main class="cover">
    <div class="cover-photo" role="img" aria-label="Silhouette of a woman in profile standing in a field at golden sunset, warm glowing sky fading to dark foreground foliage"></div>

    <p class="subtitle">A Handbook for the Woman in the Storm or Set to Begin</p>
    <div class="subtitle-rule"></div>

    <div class="seal">
      <svg width="174" height="174" viewBox="0 0 174 174" aria-hidden="true">
        <defs>
          <linearGradient id="sealGold" x1="0" y1="0" x2="1" y2="1">
            <stop offset="0" stop-color="#b88a3a"/>
            <stop offset="0.4" stop-color="#f6e3a4"/>
            <stop offset="0.7" stop-color="#d8b263"/>
            <stop offset="1" stop-color="#b88a3a"/>
          </linearGradient>
        </defs>
        <g fill="url(#sealGold)" transform="translate(87 87)">
          <rect x="-61.5" y="-61.5" width="123" height="123"/>
          <rect x="-61.5" y="-61.5" width="123" height="123" transform="rotate(11.25)"/>
          <rect x="-61.5" y="-61.5" width="123" height="123" transform="rotate(22.5)"/>
          <rect x="-61.5" y="-61.5" width="123" height="123" transform="rotate(33.75)"/>
          <rect x="-61.5" y="-61.5" width="123" height="123" transform="rotate(45)"/>
          <rect x="-61.5" y="-61.5" width="123" height="123" transform="rotate(56.25)"/>
          <rect x="-61.5" y="-61.5" width="123" height="123" transform="rotate(67.5)"/>
          <rect x="-61.5" y="-61.5" width="123" height="123" transform="rotate(78.75)"/>
          <circle r="80"/>
        </g>
      </svg>
      <div class="seal-text">A Compass<br>for Women<br>Navigating<br>Transformation</div>
    </div>

    <svg class="title" viewBox="0 0 757 1137" aria-label="Harbor Lanterns">
      <text x="59" y="807" font-size="168" textLength="635" lengthAdjust="spacingAndGlyphs">HARBOR</text>
      <text x="63" y="1003" font-size="263" textLength="631" lengthAdjust="spacingAndGlyphs">LANTERNS</text>
    </svg>

    <div class="author">
      <span class="author-rule"></span>
      <span class="author-name">DENA MORROW</span>
      <span class="author-rule"></span>
    </div>
  </main>
</body>
</html>
```